U.S. Popcorn company needs business cards

We are a popcorn company that manufactures popcorn and sells it to grocery stores worldwide. Our theme is "Americana" and our logo is U.S. route 66 which is the most famous highway in the U.S.

We would like the design to be simple and to use both sides. On the back side we would like to see just the logo and website. The front would be normal details

Target Market(s)

Wholesalers, grocers and distributors

Industry/Entity Type

Manufacture

Contact Information for Business Card

Business name: Prairie Lantern Popcorn
Phone: +1 555 308 4726
Email: Dale@prairielanternpopcorn.com
website: www.prairielanternpopcorn.com
Tag Line: "Crunch from coast to coast"
Name: Dale Whitcombe
Title: Founder/President

Requirements
Must have
• Either this design should be fun or clean and simple. I will let you show me your thougths.
Nice to have
• Anything that ties in the real Hwy Route 66.
• Colors might need to be red, white and blue incorporated.
Should not have
• Not be too busy.

```html
<!DOCTYPE html>
<html lang="en">
<head>
<meta charset="utf-8">
<title>Prairie Lantern Popcorn — Business Card</title>
<link href="https://fonts.googleapis.com/css2?family=Mulish:wght@400;600;700;800&display=swap" rel="stylesheet">
<style>
  :root {
    --stage: #e9e6e1;
    --card: #f3f2f0;
    --card-edge: #dcdad6;
    --navy: #1f3a78;
    --red: #d42a2a;
    --ink: #3a3d4a;
    --name-tint: #ece2d0;
    --title-tint: #f4f1ea;
  }
  html, body {
    margin: 0;
    width: 1200px;
    height: 1010px;
    overflow: hidden;
    background: var(--stage);
    font-family: "Mulish", sans-serif;
  }
  .business-card {
    position: absolute;
    left: 174px;
    top: 281px;
    width: 852px;
    height: 495px;
    background: linear-gradient(160deg, #f7f6f4 0%, var(--card) 60%, #ebe9e6 100%);
    border: 1px solid var(--card-edge);
    border-radius: 4px;
    box-shadow: 0 10px 30px rgba(0,0,0,0.12);
    overflow: hidden;
    color: var(--ink);
  }
  .wave-band {
    position: absolute;
    inset: 0;
    width: 100%;
    height: 100%;
  }
  .holder-name {
    position: absolute;
    right: 44px;
    top: 42px;
    margin: 0;
    font-size: 31px;
    font-weight: 700;
    color: var(--name-tint);
  }
  .holder-title {
    position: absolute;
    right: 44px;
    top: 81px;
    margin: 0;
    font-size: 18px;
    font-weight: 400;
    color: var(--title-tint);
  }
  .brand-mark {
    position: absolute;
    left: 40px;
    top: 120px;
    width: 297px;
    height: 266px;
    display: flex;
    align-items: center;
    gap: 16px;
  }
  .brand-dot {
    flex: 0 0 auto;
    width: 44px;
    height: 44px;
    border-radius: 50%;
    background: var(--red);
  }
  .brand-name {
    margin: 0;
    font-size: 38px;
    line-height: 1.12;
    font-weight: 800;
    color: var(--navy);
  }
  .tagline {
    position: absolute;
    left: 40px;
    top: 421px;
    margin: 0;
    font-size: 21px;
    font-weight: 400;
    color: var(--ink);
  }
  .tagline .lead {
    color: var(--red);
    font-weight: 800;
  }
  .contact-list {
    position: absolute;
    right: 42px;
    top: 362px;
    margin: 0;
    padding: 0;
    list-style: none;
    text-align: right;
  }
  .contact-list li {
    display: flex;
    justify-content: flex-end;
    align-items: center;
    gap: 9px;
    height: 29px;
    font-size: 20px;
    color: var(--ink);
  }
  .contact-list .domain { color: var(--red); }
  .contact-icon {
    width: 18px;
    height: 18px;
    flex: 0 0 auto;
  }
</style>
</head>
<body>
  <div class="business-card">
    <svg class="wave-band" viewBox="0 0 818 475" preserveAspectRatio="none" aria-hidden="true">
      <path d="M0 0 H818 V192 C700 192 575 160 445 90 C340 35 160 12 0 32 Z" fill="var(--navy)"/>
      <path d="M0 58 C150 12 320 8 440 40 C320 26 150 38 0 94 Z" fill="var(--red)"/>
      <path d="M70 58 C250 40 430 68 570 140 C670 190 745 218 818 222" fill="none" stroke="var(--red)" stroke-width="8"/>
    </svg>

    <h1 class="holder-name">Dale Whitcombe</h1>
    <p class="holder-title">Founder/President</p>

    <div class="brand-mark">
      <span class="brand-dot"></span>
      <p class="brand-name">Prairie Lantern Popcorn</p>
    </div>

    <p class="tagline">"<span class="lead">Crunch</span> from coast to coast"</p>

    <ul class="contact-list">
      <li>+1 555 308 4726
        <svg class="contact-icon" viewBox="0 0 20 20"><path d="M2 8 C2 4 18 4 18 8 L15 9 L13 7 H7 L5 9 Z M5 10 H15 L17 17 H3 Z" fill="var(--red)"/><circle cx="10" cy="13" r="2" fill="#fff"/></svg>
      </li>
      <li>Dale@prairielanternpopcorn.com
        <svg class="contact-icon" viewBox="0 0 20 20"><rect x="1" y="4" width="18" height="12" fill="var(--red)"/><path d="M1 4 L10 11 L19 4" fill="none" stroke="#fff" stroke-width="1.5"/></svg>
      </li>
      <li><span>www.<span class="domain">prairielanternpopcorn</span>.com</span>
        <svg class="contact-icon" viewBox="0 0 20 20"><circle cx="10" cy="10" r="8.5" fill="var(--red)"/><path d="M1.5 10 H18.5 M10 1.5 V18.5 M10 1.5 C5 6 5 14 10 18.5 M10 1.5 C15 6 15 14 10 18.5" fill="none" stroke="#fff" stroke-width="1.2"/></svg>
      </li>
    </ul>
  </div>
</body>
</html>
```